A clean crisp business card for a Landscape Construction company. Designed to be easy to read contact/ info and also be appealing/interesting, unlike a traditional business card.

Industry/Entity Type

Landscape Construction

Contact Information for Business Card

Company name : Brambleford Landscape Construction, phone number: (877) 62Vista, website:Bramblefordyards.example, Email, sales@bramblefordyards.example

Requirements
Nice to have
• Luxurious finishes/ details…. Icons or emblems next to contact info
Should not have
• Clipart or general pictures

```html
<!DOCTYPE html>
<html lang="en">
<head>
<meta charset="utf-8">
<title>Brambleford Landscape Construction – Business Card</title>
<link href="https://fonts.googleapis.com/css2?family=Cinzel:wght@600;700&family=Arimo:wght@400&display=swap" rel="stylesheet">
<style>
  :root {
    --bg: #2b2d30;
    --brand-blue: #2468b4;
    --deep-blue: #1b4f8e;
    --leaf-green: #9ccb3b;
    --paper: #ffffff;
    --ink-light: #ffffff;
  }
  * { margin: 0; padding: 0; box-sizing: border-box; }
  html, body { width: 1200px; height: 900px; overflow: hidden; }
  body { background: var(--bg); position: relative; font-family: "Arimo", Arial, sans-serif; }

  .card {
    position: absolute;
    width: 620px; height: 354px;
    border-radius: 22px;
    overflow: hidden;
  }

  /* Back side */
  .card--back { left: 540px; top: 50px; background: var(--brand-blue); }
  .card--back .wordmark {
    position: absolute; right: 44px; top: 50px;
    display: flex; align-items: center; gap: 14px;
    color: var(--deep-blue);
  }
  .wordmark-dot {
    width: 18px; height: 18px; border-radius: 50%;
    background: currentColor; flex: none;
  }
  .wordmark-text {
    font-family: "Cinzel", serif; font-weight: 600;
    line-height: 1.05;
  }
  .wordmark-text .primary { display: block; }
  .wordmark-text .secondary { display: block; letter-spacing: 0.18em; }
  .card--back .primary { font-size: 40px; }
  .card--back .secondary { font-size: 12.5px; }

  /* Front side */
  .card--front { left: 60px; top: 470px; background: var(--paper); }
  .card-wave { position: absolute; inset: 0; }
  .card--front .wordmark {
    position: absolute; left: 34px; top: 48px;
    display: flex; align-items: center; gap: 10px;
    color: var(--brand-blue);
  }
  .card--front .primary { font-size: 32px; }
  .card--front .secondary { font-size: 10px; }

  .address {
    position: absolute; left: 32px; bottom: 52px;
    color: var(--ink-light); font-size: 17px; line-height: 1.35;
    font-style: normal;
  }
  .contact {
    position: absolute; right: 48px; bottom: 20px;
    text-align: right; color: var(--ink-light);
  }
  .contact .person {
    font-family: "Cinzel", serif; font-weight: 700;
    color: var(--leaf-green); font-size: 23px; letter-spacing: 0.04em;
    line-height: 1.15;
  }
  .contact .role { font-size: 15px; line-height: 1.2; margin-bottom: 4px; }
  .contact-row {
    display: flex; justify-content: flex-end; align-items: center;
    gap: 9px; font-size: 14px; line-height: 1.4;
  }
  .contact-row svg { width: 13px; height: 13px; fill: var(--ink-light); flex: none; }
</style>
</head>
<body>

<section class="card card--back" aria-label="Business card back">
  <div class="wordmark">
    <span class="wordmark-dot"></span>
    <span class="wordmark-text">
      <span class="primary">Brambleford</span>
      <span class="secondary">Landscape Construction</span>
    </span>
  </div>
</section>

<section class="card card--front" aria-label="Business card front">
  <svg class="card-wave" viewBox="0 0 620 354" preserveAspectRatio="none" aria-hidden="true">
    <path d="M0,72 C6,165 70,192 260,197 C420,201 520,205 560,212 C590,220 610,240 620,262 L620,354 L0,354 Z" fill="var(--brand-blue)"/>
    <path d="M4,62 C10,155 72,183 260,188 C420,192 520,196 572,206" fill="none" stroke="var(--leaf-green)" stroke-width="7"/>
  </svg>

  <div class="wordmark">
    <span class="wordmark-dot"></span>
    <span class="wordmark-text">
      <span class="primary">Brambleford</span>
      <span class="secondary">Landscape Construction</span>
    </span>
  </div>

  <address class="address">
    4410 W. Larkin Avenue<br>
    Region Name, AB 40217
  </address>

  <div class="contact">
    <div class="person">OWEN TARROW</div>
    <div class="role">Founder</div>
    <div class="contact-row">(877) 62Vista
      <svg viewBox="0 0 16 16"><path d="M3.6 1.2l2.3 2.6-1.4 1.8c.9 2 2.6 3.7 4.6 4.6l1.8-1.4 2.6 2.3-1.3 2.3C7.4 13.5 2.5 8.6 1.3 3.8z"/></svg>
    </div>
    <div class="contact-row">sales@bramblefordyards.example
      <svg viewBox="0 0 16 16"><path d="M1 3h14v10H1z M1.6 3.6L8 8.6l6.4-5" fill="none" stroke="#fff" stroke-width="1.4"/></svg>
    </div>
    <div class="contact-row">bramblefordyards.example
      <svg viewBox="0 0 16 16"><circle cx="8" cy="8" r="6.3" fill="none" stroke="#fff" stroke-width="1.4"/><path d="M1.7 8h12.6M8 1.7c-3 3.4-3 9.2 0 12.6M8 1.7c3 3.4 3 9.2 0 12.6" fill="none" stroke="#fff" stroke-width="1.1"/></svg>
    </div>
  </div>
</section>

</body>
</html>
```